Vorn upkeep KT Solar Venture

Solar power system install
Services and maintenance
wiring, Rewinding and Renovation
Switch Board Upgrade
Power and lighting point
t doesn’t matter how much you spend on quality parts, your solar system will let you down if your design and installation are sub-par. Have your solar system tailored and installed by our Master Electrician and Bright Grid Guild Accredited team.

Target Market(s)

sales and installed

Industry/Entity Type

Solar install and retailer

Contact Information for Business Card

Name , Email, Phone Number ,Business address,

Font styles to use
Serif

Colors
0054AA
0677BA
7BADD7
CADEEF
E8F1F8

Requirements
Must have
• clear and bright
Nice to have
• new design
Should not have
• unclear pictures

```html
<!DOCTYPE html>
<html lang="en">
<head>
<meta charset="utf-8">
<title>KT Solar Venture – Business Card</title>
<link href="https://fonts.googleapis.com/css2?family=Roboto:wght@400;500;700&display=swap" rel="stylesheet">
<style>
  :root {
    --bg: #2c2c2c;
    --blue-deep: #0054aa;
    --blue-mid: #0677ba;
    --blue-soft: #7badd7;
    --green: #2fa043;
    --green-light: #7cc242;
    --sun: #f2b531;
    --band: #ececec;
    --card-white: #f1f2f3;
    --ink: #1f1f1f;
    --white: #ffffff;
  }
  * { margin: 0; padding: 0; box-sizing: border-box; }
  html, body {
    width: 1200px; height: 1138px; overflow: hidden;
    background: var(--bg);
    font-family: "Roboto", sans-serif;
  }
  .card {
    position: absolute;
    width: 624px; height: 376px;
    border-radius: 16px;
    overflow: hidden;
  }
  /* front */
  .card-front {
    left: 274px; top: 185px;
    background: linear-gradient(115deg, var(--blue-mid) 0%, #0f8a9a 45%, #3ea75f 75%, #6ab23a 100%);
  }
  .brand {
    position: absolute;
    display: flex; align-items: center; gap: 18px;
  }
  .brand-dot {
    width: 64px; height: 64px; border-radius: 50%;
    background: var(--sun);
    flex: none;
  }
  .brand-name {
    font-weight: 700;
    text-transform: uppercase;
    line-height: 1.08;
    letter-spacing: 0.5px;
  }
  .card-front .brand { left: 120px; top: 84px; }
  .card-front .brand-name { color: var(--white); font-size: 32px; }
  .service-band {
    position: absolute; left: 0; top: 240px;
    width: 100%; height: 74px;
    background: var(--band);
    display: flex; flex-direction: column; justify-content: center; align-items: center;
    color: var(--ink); font-size: 16px; line-height: 23px;
  }
  .front-web {
    position: absolute; left: 0; top: 333px; width: 100%;
    display: flex; justify-content: center; align-items: center; gap: 24px;
    color: var(--white); font-size: 15px;
  }
  .front-web .rule { width: 80px; height: 2px; background: rgba(255,255,255,0.75); }

  /* back */
  .card-back {
    left: 276px; top: 608px;
    background: var(--card-white);
  }
  .card-back .waves { position: absolute; inset: 0; width: 100%; height: 100%; }
  .card-back .brand { left: 50px; top: 110px; flex-direction: column; align-items: flex-start; gap: 14px; }
  .card-back .brand-name { color: var(--blue-deep); font-size: 29px; }
  .person {
    position: absolute; right: 28px; top: 40px;
    text-align: right; color: var(--ink);
  }
  .person-name { color: var(--blue-deep); font-size: 24px; font-weight: 700; }
  .person-role { font-size: 15px; margin-top: 4px; }
  .person-address { font-size: 15px; line-height: 24px; margin-top: 20px; }
  .contacts {
    position: absolute; right: 24px; top: 268px;
    list-style: none; color: var(--white); font-size: 15px;
  }
  .contacts li {
    display: flex; justify-content: flex-end; align-items: center; gap: 12px;
    height: 24px;
  }
  .contacts svg { width: 14px; height: 14px; fill: none; stroke: var(--white); stroke-width: 1.6; }
</style>
</head>
<body>

<section class="card card-front" aria-label="Business card front">
  <div class="brand">
    <span class="brand-dot"></span>
    <div class="brand-name">Vorn Upkeep<br>Solar Venture</div>
  </div>
  <div class="service-band">
    <p>Solar Power System Install&nbsp; | &nbsp;Wiring, Rewinding &amp; Renovation</p>
    <p>Services &amp; Maintenance&nbsp; | &nbsp;Switch Board Upgrade&nbsp; | &nbsp;Power &amp; Lighting Point</p>
  </div>
  <div class="front-web">
    <span class="rule"></span>
    <span>www.ktsolarventure.com</span>
    <span class="rule"></span>
  </div>
</section>

<section class="card card-back" aria-label="Business card back">
  <svg class="waves" viewBox="0 0 624 376" preserveAspectRatio="none" aria-hidden="true">
    <path d="M0 312 C120 362 260 352 380 292 C460 252 540 232 624 242 L624 376 L0 376 Z" fill="var(--blue-mid)"/>
    <path d="M0 300 C120 336 250 330 370 272 C460 228 550 208 624 214 L624 226 C550 222 470 242 382 284 C262 340 120 346 0 316 Z" fill="var(--green)"/>
    <path d="M0 272 C90 300 210 312 310 300 C210 322 90 316 0 292 Z" fill="var(--green-light)"/>
  </svg>

  <div class="brand">
    <span class="brand-dot"></span>
    <div class="brand-name">Vorn Upkeep<br>Solar Venture</div>
  </div>

  <div class="person">
    <p class="person-name">Mara Lenn Hollis</p>
    <p class="person-role">Managing Director</p>
    <p class="person-address">48 Copper Lane, Fernvale,<br>Any Town, US 20417</p>
  </div>

  <ul class="contacts">
    <li>555-014-2290
      <svg viewBox="0 0 16 16"><path d="M3 2h3l1 3-2 1.5a8 8 0 0 0 4.5 4.5L11 9l3 1v3a1.5 1.5 0 0 1-1.5 1.5A11 11 0 0 1 1.5 3.5 1.5 1.5 0 0 1 3 2z"/></svg>
    </li>
    <li>mara@ktsolarventure.com
      <svg viewBox="0 0 16 16"><rect x="1.5" y="3.5" width="13" height="9"/><path d="M1.5 3.5 8 9l6.5-5.5"/></svg>
    </li>
    <li>www.ktsolarventure.com
      <svg viewBox="0 0 16 16"><circle cx="8" cy="8" r="6.5"/><ellipse cx="8" cy="8" rx="3" ry="6.5"/><path d="M1.5 8h13"/></svg>
    </li>
  </ul>
</section>

</body>
</html>
```